Timber Crest Construction Needs business card

Hey we are in need of business card designs. I have upload our logo as a guideline, but free feel to run with it or come up with something unique.
Pls have fun with it and be creative. the name says it all!
i will give some directions after i see a few entries..
Updates
Logo source file has been uploaded..
Hey because of the logo is so colourful already.
Can we have a few submissions with less colour.
Also we are looking for clever/hidden/descriptive business card.

```html
<!DOCTYPE html>
<html lang="en">
<head>
<meta charset="utf-8">
<title>Timber Crest Construction – Business Card</title>
<link rel="stylesheet" href="https://fonts.googleapis.com/css2?family=Josefin+Sans:wght@400;600;700&display=swap">
<style>
  :root {
    --page-bg: #e6e4e1;
    --card-black: #0a0a0a;
    --card-white: #f3f3f3;
    --ink: #2b2b2b;
    --ink-soft: #4a4a4a;
    --accent-red: #e3232b;
    --block-blue: #1179c3;
    --block-yellow: #f2c10f;
    --block-green: #0f8a3e;
    --block-grey: #3c3d3f;
    --name-grey: #8c8c8c;
  }
  * { box-sizing: border-box; margin: 0; padding: 0; }
  html, body {
    width: 1200px; height: 900px; overflow: hidden;
    background: var(--page-bg);
    font-family: "Josefin Sans", sans-serif;
  }
  .canvas {
    width: 1200px; height: 900px;
    display: flex; flex-direction: column; align-items: center; justify-content: center;
    gap: 50px;
  }
  .card {
    width: 630px; height: 360px;
    position: relative; overflow: hidden;
    box-shadow: 0 10px 28px rgba(0,0,0,0.18);
  }
  .card-front {
    background: var(--card-black);
    display: flex; align-items: center; justify-content: center; gap: 16px;
  }
  .brand-square {
    width: 26px; height: 26px; background: var(--name-grey);
  }
  .brand-name {
    color: var(--name-grey);
    font-weight: 700; font-size: 30px; letter-spacing: 2px; text-transform: uppercase;
  }
  .card-back { background: var(--card-white); }
  .contact {
    position: absolute; left: 44px; top: 44px;
    color: var(--ink);
  }
  .person-name {
    font-weight: 700; font-size: 15px; letter-spacing: 2.5px; text-transform: uppercase;
  }
  .person-role {
    color: var(--accent-red);
    font-size: 11px; letter-spacing: 2.5px; text-transform: uppercase; margin-top: 4px;
  }
  .address {
    margin-top: 26px;
    font-size: 12px; letter-spacing: 2.5px; line-height: 1.6; text-transform: uppercase;
    color: var(--ink-soft);
  }
  .contact-list { list-style: none; margin-top: 22px; }
  .contact-list li {
    display: flex; align-items: center; gap: 12px;
    font-size: 12.5px; letter-spacing: 2px; line-height: 1;
    color: var(--ink-soft); margin-bottom: 11px;
  }
  .contact-icon { width: 14px; height: 14px; flex: none; }
  .block-field {
    position: absolute; right: 0; bottom: 0;
    width: 400px; height: 300px;
    clip-path: polygon(100% 0, 100% 100%, 0 100%, 0 78%, 40% 40%, 62% 10%);
    background: linear-gradient(135deg,
      var(--block-green) 0%, var(--block-yellow) 25%, var(--accent-red) 45%,
      var(--block-blue) 65%, var(--block-grey) 85%);
    opacity: 0.85;
  }
</style>
</head>
<body>
<main class="canvas">
  <section class="card card-front" aria-label="Card front">
    <span class="brand-square"></span>
    <span class="brand-name">Timber Crest Construction</span>
  </section>

  <section class="card card-back" aria-label="Card back">
    <div class="contact">
      <p class="person-name">Marta Keene</p>
      <p class="person-role">Director</p>
      <p class="address">Shop 2, 118-120 Harbour<br>Road Westfield North</p>
      <ul class="contact-list">
        <li>
          <svg class="contact-icon" viewBox="0 0 14 14" aria-hidden="true">
            <circle cx="7" cy="7" r="7" fill="var(--accent-red)"/>
            <path d="M4.3 3.6c.4-.4.9-.3 1.1.1l.6 1.1c.2.3.1.6-.2.8l-.4.3c.3.8.9 1.5 1.7 1.9l.3-.4c.2-.3.6-.3.8-.1l1 .7c.4.3.4.8 0 1.1l-.5.5c-2 .4-5.1-2.6-4.8-4.7z" fill="#fff"/>
          </svg>
          9517 2204
        </li>
        <li>
          <svg class="contact-icon" viewBox="0 0 14 14" aria-hidden="true">
            <circle cx="7" cy="7" r="7" fill="var(--accent-red)"/>
            <rect x="4" y="4" width="6" height="6" rx="0.6" fill="none" stroke="#fff" stroke-width="1"/>
            <line x1="5.5" y1="8.5" x2="8.5" y2="8.5" stroke="#fff" stroke-width="0.8"/>
          </svg>
          9517 2290
        </li>
        <li>
          <svg class="contact-icon" viewBox="0 0 14 14" aria-hidden="true">
            <circle cx="7" cy="7" r="7" fill="var(--accent-red)"/>
            <rect x="3.5" y="4.5" width="7" height="5" fill="none" stroke="#fff" stroke-width="1"/>
            <path d="M3.5 4.5 7 7.3l3.5-2.8" fill="none" stroke="#fff" stroke-width="1"/>
          </svg>
          marta@keenebuild.com
        </li>
        <li>
          <svg class="contact-icon" viewBox="0 0 14 14" aria-hidden="true">
            <circle cx="7" cy="7" r="7" fill="var(--accent-red)"/>
            <circle cx="7" cy="7" r="3.5" fill="none" stroke="#fff" stroke-width="0.9"/>
            <ellipse cx="7" cy="7" rx="1.5" ry="3.5" fill="none" stroke="#fff" stroke-width="0.8"/>
            <line x1="3.5" y1="7" x2="10.5" y2="7" stroke="#fff" stroke-width="0.8"/>
          </svg>
          www.keenebuild.com
        </li>
      </ul>
    </div>
    <div class="block-field" role="img" aria-label="Decorative field of coloured building blocks in green, yellow, red, blue and charcoal"></div>
  </section>
</main>
</body>
</html>
```